PostCard Design Project

I am making a mailing postcard
I am having the mailing printed using 4 color foil on certain parts.
I am looking for a design that maximizes the foil process where certain parts are done in foil to grab the customers attention (example: if there is a car on the postcard the headlights would be done in foil) .
I am targeting some industries, (auto, real estate, medical, beauty) I would like the post card to have examples of postcard ideas for 2 or 3 of these industries.
specs:
the postcard should be atleast 6.5x9 up to 8.5x11, I don't want to restrict the space for the creative as I don't want everything to look like a huge mess. both sides will be used.
the piece is a direct mail piece so it has to meet requirements of https://www.mailvantor.com/business/pdf/quick-reference-guide.pdf
text will be
"business with no limits, meet mailing with no addresses, gain new customers through "Open Porch Route Drop" reach new customers at their home without needing their address. "
I also want some current print specials I am running included.
-double your order FREE (order 500 business cards and get 1000)
-250 100lb gloss stock brochures 99.00
-business packages (cards, envelopes and letterhead) 299
-1000 flyers 140.40
-5000 postcards 179.99
A list of services
banners
booklets
brochures
business cards
calendars
catalogs
CD/DVD packages
envelopes
event tickets
flyers
hangtags
postcards
posters
presentation folders
rack cards
labels
table tents
window cling and decal
"order 24/7 orders@inkwillow.com" must be included
my logo is InkWillow will be supplied later
ive received some great designs. however Im looking for something a little more modern like some zorvel would put out. if the amount of words is too much please feel free to edit. also an idea i had for the list of services i offer is to have it transparent yet readable as the background of the postcard some small some big but covering the entire backgroud. you can then design on top of that with other thing. just an early morning thought
Reason: I have uploaded a sketch of my idea, please take time to look at it for an accurate depiction of what im looking for. feel free to add elements that make it pop off the page
Reason: We are getting close i will be providing feed back today

```html
<!DOCTYPE html>
<html lang="en">
<head>
<meta charset="utf-8">
<title>InkWillow Mailing Postcard</title>
<link rel="stylesheet" href="https://fonts.googleapis.com/css2?family=Arimo:wght@400;700&family=Open+Sans:wdth,wght@75..100,400..800&display=swap">
<style>
  :root {
    --page: #000000;
    --card-blue: #2b8ccc;
    --white: #ffffff;
    --ink: #1a1a1a;
    --oval-text: #4a4a4a;
    --accent-yellow: #f2e61b;
    --logo-blue: #2a6fb6;
    --logo-dot: #e8932c;
    --teeth-light: #f2d3cb;
    --teeth-deep: #b8545c;
    --portrait-light: #f4f1f0;
    --portrait-skin: #e3c2b0;
    --portrait-hair: #4a2f25;
    --car-red: #c8141c;
    --car-dark: #1c1c1e;
  }
  * { margin: 0; padding: 0; box-sizing: border-box; }
  html, body { width: 835px; height: 1200px; overflow: hidden; background: var(--page); }
  .canvas { position: relative; width: 835px; height: 1200px; background: var(--page); font-family: "Open Sans", Arial, sans-serif; }

  .side { position: absolute; left: 64px; width: 708px; background: var(--card-blue); overflow: hidden; }
  .side--front { top: 42px; height: 533px; }
  .side--back { top: 619px; height: 515px; }

  /* Front */
  .headline { position: absolute; left: 22px; top: 40px; color: var(--white); font-weight: 700; }
  .headline__line { display: block; font-size: 40px; line-height: 48px; letter-spacing: -0.5px; font-stretch: 92%; }
  .headline__shine { display: block; font-size: 78px; line-height: 80px; font-weight: 700; letter-spacing: -2px; font-stretch: 75%; }

  .logo-box { position: absolute; left: 457px; top: 35px; width: 179px; height: 62px; background: var(--white);
    display: flex; align-items: center; justify-content: center; gap: 8px; }
  .logo-box__dot { width: 24px; height: 24px; border-radius: 50%; background: var(--logo-dot); }
  .logo-box__name { font-size: 27px; font-weight: 400; color: var(--logo-blue); letter-spacing: -0.5px; }

  .photo { position: absolute; }
  .photo--smile { left: 381px; top: 111px; width: 327px; height: 192px;
    background: radial-gradient(ellipse at 45% 65%, var(--white) 0%, var(--teeth-light) 22%, var(--teeth-deep) 48%, var(--teeth-light) 80%); }
  .photo--portrait { left: 134px; top: 231px; width: 300px; height: 191px;
    background: radial-gradient(ellipse at 52% 45%, var(--portrait-skin) 0%, var(--portrait-skin) 25%, var(--portrait-hair) 42%, var(--portrait-light) 60%); }
  .photo--headlight { left: 390px; top: 316px; width: 291px; height: 197px;
    background: linear-gradient(200deg, var(--car-red) 0%, var(--car-red) 30%, var(--car-dark) 55%, var(--car-dark) 100%); }

  .order-line { position: absolute; left: 22px; top: 436px; color: var(--white); font-weight: 700; font-size: 27px; line-height: 40px; letter-spacing: -0.5px; font-stretch: 88%; }

  /* Back */
  .intro { position: absolute; left: 17px; top: 20px; width: 310px; color: var(--white); font-size: 15px; line-height: 21px; }
  .intro__highlight { color: var(--accent-yellow); }

  .indicia { position: absolute; left: 601px; top: 25px; width: 83px; height: 87px; background: var(--white); border: 1px solid var(--ink);
    text-align: center; font-family: "Arimo", Arial, sans-serif; font-size: 10px; line-height: 13px; color: var(--ink); padding-top: 6px; }
  .indicia__paid { font-size: 14px; line-height: 17px; }

  .address-box { position: absolute; left: 522px; top: 128px; width: 163px; height: 81px; background: var(--white); border: 1px solid var(--ink);
    font-family: "Arimo", Arial, sans-serif; font-size: 15px; line-height: 19px; color: var(--ink); padding: 19px 0 0 18px; }

  .services { position: absolute; left: 354px; top: 101px; }
  .services__title { color: var(--accent-yellow); font-weight: 700; font-size: 34px; line-height: 40px; margin-left: 1px; }
  .services__list { list-style: none; margin-top: 3px; }
  .services__item { position: relative; padding-left: 14px; color: var(--white); font-size: 15px; line-height: 22.4px; }
  .services__item::before { content: ""; position: absolute; left: 0; top: 9px; width: 5px; height: 5px; border-radius: 50%; background: var(--dot); }

  .special { position: absolute; background: var(--white); border-radius: 50%; display: flex; align-items: center; justify-content: center;
    text-align: center; font-family: "Arimo", Arial, sans-serif; font-weight: 700; font-size: 14.5px; line-height: 18px; color: var(--oval-text); }
  .special--double { left: 6px; top: 140px; width: 190px; height: 93px; }
  .special--brochures { left: 180px; top: 216px; width: 160px; height: 98px; }
  .special--postcards { left: 6px; top: 336px; width: 139px; height: 92px; }
  .special--packages { left: 152px; top: 316px; width: 188px; height: 123px; }
  .special--flyers { left: 71px; top: 436px; width: 114px; height: 72px; }

  .specials-label { position: absolute; left: 18px; top: 268px; width: 157px; text-align: center; color: var(--accent-yellow);
    font-weight: 700; font-size: 22px; line-height: 24px; font-stretch: 75%; white-space: nowrap; }
</style>
</head>
<body>
<div class="canvas">

  <section class="side side--front">
    <h1 class="headline">
      <span class="headline__line">Let Us Help</span>
      <span class="headline__line">Your Business</span>
      <span class="headline__shine">SHINE!</span>
    </h1>

    <div class="logo-box">
      <span class="logo-box__dot"></span>
      <span class="logo-box__name">InkWillow</span>
    </div>

    <div class="photo photo--smile" role="img" aria-label="Close-up photo of a smiling mouth with dental braces"></div>
    <div class="photo photo--portrait" role="img" aria-label="Beauty portrait photo of a woman on a light background"></div>
    <div class="photo photo--headlight" role="img" aria-label="Close-up photo of a red sports car headlight and grille"></div>

    <p class="order-line">24 hr/ 7day<br>Order@inkwillow.com</p>
  </section>

  <section class="side side--back">
    <p class="intro">Business with no limits, meet mailing with no addresses, gain new customers through <span class="intro__highlight">"Open Porch Route Drop"</span><br>reach new customers at their home without needing their address.</p>

    <div class="indicia">PRSRT STD<br>ECRWSS<br>U.S.POSTAGE<br><span class="indicia__paid">PAID</span><br>OPRD Retail</div>

    <div class="address-box">Local<br>Postal Customer</div>

    <div class="special special--double">Double your<br>order FREE<br>(order 500 business<br>cards and get 1000)</div>
    <div class="special special--brochures">250 100lb gloss<br>stock<br>brochures 99.00</div>
    <p class="specials-label">current specials<br>print</p>
    <div class="special special--postcards">5000 postcards<br>179.99</div>
    <div class="special special--packages">Business packages<br>(cards, envelopes<br>and letterhead) 299</div>
    <div class="special special--flyers">1000 flyers<br>140.40</div>

    <div class="services">
      <h2 class="services__title">Services</h2>
      <ul class="services__list">
        <li class="services__item" style="--dot:#7fd0f0">Banners</li>
        <li class="services__item" style="--dot:#9ad7f2">Booklets</li>
        <li class="services__item" style="--dot:#5aaee0">Brochures</li>
        <li class="services__item" style="--dot:#e0338a">Business cards</li>
        <li class="services__item" style="--dot:#f2e61b">Calendars</li>
        <li class="services__item" style="--dot:#e8433c">Catalogs</li>
        <li class="services__item" style="--dot:#f08a2c">CD/DVD packages</li>
        <li class="services__item" style="--dot:#e8433c">Envelopes</li>
        <li class="services__item" style="--dot:#a4d43a">Event tickets</li>
        <li class="services__item" style="--dot:#c8e04a">Flyers</li>
        <li class="services__item" style="--dot:#2fa84a">Hangtags</li>
        <li class="services__item" style="--dot:#e8433c">Postcards</li>
        <li class="services__item" style="--dot:#b8dff2">Posters</li>
        <li class="services__item" style="--dot:#1d3f8a">Presentation folders</li>
        <li class="services__item" style="--dot:#7a3fa0">Rackcards</li>
        <li class="services__item" style="--dot:#b0b0b0">Labels</li>
      </ul>
    </div>
  </section>

</div>
</body>
</html>
```